Redesign 2016 Digital Marketing Website and Convert to Wordpress

Technology needed to integrate:

- redesign and convert to wordpress
- gravity forms
- malware and hacker defense / honeypot (must be very secure from hackers)
- I want gravity forms to be a flow that asks many questions with icons and progress bar.
- 1 home page design
- 1 blog design
- 1 design for internal page content
- 1 multi step gravity form
I want to focus on SMB's. We are a marketing agency thats been around since 2016.

Site is: tallpine.agency

I am looking to redesign the homepage, blog page and services page. The services page will be a template for all inner pages of the site. All content needs to be moved into the new design.

I want to get ride of the weird video.

I need you to install gravity forms pro model so we can pass utms.

I need the gravity form to be a multi step form with icons.

All "contact us" or "get a free assesments" call to actions will go to this form only.

step 1:
what is your website

step 2:
what industry are you in
- option
- Home Services
- Legal
- Ecommerce
- Lead Gen

No matter which one they select its going to produce a differnt calculator for them.

Law:
How many leads did you get last month
how much is each ase worth on average
How much revenue do you want to make

Home servicse:
How many bookings did you get last month
How much is each service worht on average
How much revenue do you wangt to make

Ecommerce:
What is your average order value
How muny purchases did you have last month
How much revenue did you drive
How much revenue do you want to drive

For lead gen:
How many leads did you get lawt month
How much revenue did they generate

Step 3:
What is your current advertising budget

step 4:
Do you have a CRM and if so what is it

Step 5:
What is your personal informagtion
name
email
phone

Let me know if this is enough to get you going

Small and medium sized law firms, ecommerce, home services and lead gen customers.

We are a digital marketing agency

• Use whats on the current site and improve upon it

• Must be very secure, developed into a wordpress website. using gravity forms. remove my photo and my staffs photo, depersonalize it so it doesnt mention me or sam crolley. Use the same color scheme. I am looking to redesign the homepage, blog page and services page. The services page will be a template for all inner pages of the site. All content needs to be moved into the new design. I want to get ride of the weird video. I need you to install gravity forms pro model so we can pass utms. I need the gravity form to be a multi step form with icons. All "contact us" or "get a free assesments" call to actions will go to this form only. step 1: what is your website step 2: what industry are you in - option - Home Services - Legal - Ecommerce - Lead Gen No matter which one they select its going to produce a differnt calculator for them. Law: How many leads did you get last month how much is each ase worth on average How much revenue do you want to make Home servicse: How many bookings did you get last month How much is each service worht on average How much revenue do you wangt to make Ecommerce: What is your average order value How muny purchases did you have last month How much revenue did you drive How much revenue do you want to drive For lead gen: How many leads did you get lawt month How much revenue did they generate How much revenue do you want to make Step 3: What is your current advertising budget step 4: Do you have a CRM and if so what is it Step 5: What is your personal informagtion name email phone Let me know if this is enough to get you going
• SHOULD NOT BE SLOPPY, I AM LOOKING FOR ATTENTION TO DETAIL.

```html
<!DOCTYPE html>
<html lang="en">
<head>
<meta charset="utf-8">
<title>Out of Home Advertising — Tall Pine</title>
<link rel="stylesheet" href="https://fonts.googleapis.com/css2?family=Montserrat:wght@400;500;600;700;800&display=swap">
<style>
:root{
  --red:#7a1416;
  --red-deep:#5e0d0f;
  --red-bright:#b3262a;
  --ink:#141414;
  --text:#2b2b2b;
  --muted:#6b6b6b;
  --grey-band:#e3e3e3;
  --line:#cfcfcf;
  --white:#ffffff;
  --pink:#f3e3e3;
}
*{margin:0;padding:0;box-sizing:border-box}
html,body{width:1200px;height:4184px;overflow:hidden;background:var(--white)}
body{font-family:"Montserrat",Arial,sans-serif;color:var(--text)}
.page{position:relative;width:1200px;height:4184px;overflow:hidden}
.abs{position:absolute}
a{color:inherit;text-decoration:none}

/* header */
.site-header{position:absolute;left:0;top:0;width:1200px;height:67px;background:var(--white);box-shadow:0 1px 0 #e6e6e6}
.brand{position:absolute;display:flex;align-items:center;gap:12px}
.brand-mark{width:52px;height:52px;border-radius:50%;background:var(--red)}
.brand-name{font-weight:500;font-size:22px;letter-spacing:3px;color:var(--red)}
.main-nav{position:absolute;top:23px;left:382px;display:flex;gap:0}
.main-nav a{position:absolute;font-size:13.5px;font-weight:600;color:var(--ink);white-space:nowrap}
.main-nav a.active::after{content:"";position:absolute;left:14px;right:14px;bottom:-8px;height:2px;background:var(--ink)}
.header-cta{position:absolute;right:0;top:0;width:231px;height:67px;background:var(--red);clip-path:polygon(18px 0,100% 0,100% 100%,0 100%);color:var(--white);padding:16px 0 0 44px}
.header-cta strong{display:block;font-size:12.5px;font-weight:700;letter-spacing:.2px}
.header-cta span{display:block;font-size:10.5px;margin-top:2px}

/* hero */
.hero{position:absolute;left:0;top:67px;width:1200px;height:420px;background:radial-gradient(ellipse at 60% 75%,#3a3a3a 0%,#1c1c1c 45%,#111 100%);text-align:center;color:var(--white)}
.hero-eyebrow{position:absolute;left:0;right:0;top:122px;font-size:29px;font-weight:400;letter-spacing:1px}
.hero-title{position:absolute;left:0;right:0;top:154px;font-size:44px;font-weight:500;letter-spacing:1.5px}
.btn{display:inline-flex;align-items:center;justify-content:center;font-weight:700;text-transform:uppercase;border-radius:40px;white-space:nowrap}
.btn-red{background:var(--red);color:var(--white)}
.btn-outline{border:2px solid var(--white);color:var(--white)}
.hero .btn{position:absolute;left:463px;top:225px;width:274px;height:60px;font-size:17px}

/* intro */
.intro-photo-ring{position:absolute;left:92px;top:590px;width:460px;height:460px;border-radius:50%;border:2px solid #d9d9d9}
.intro-arc{position:absolute;left:92px;top:590px}
.intro-photo{position:absolute;left:104px;top:602px;width:436px;height:436px;border-radius:50%;background:linear-gradient(135deg,#dfe8f0 0%,#c9d4dc 45%,#a9b1b7 100%)}
.section-title{font-size:34px;font-weight:500;line-height:38px;color:var(--ink);letter-spacing:.5px}
.section-title em{font-style:normal;font-weight:600;color:var(--red);display:block}
.intro-copy{position:absolute;left:593px;top:594px;width:535px}
.rule{height:2px;background:var(--red);width:155px}
.intro-copy .rule{margin-top:20px}
.intro-copy p{font-size:14.6px;line-height:19.2px;color:var(--text);margin-top:32px}
.intro-copy p + p{margin-top:38px}

/* panels */
.panel{position:absolute;top:1113px;height:465px;text-align:center;color:var(--white)}
.panel-dark{left:0;width:598px;background:linear-gradient(180deg,#3d3d3d 0%,#2a2a2a 100%)}
.panel-red{left:598px;width:602px;background:linear-gradient(135deg,#8a181b 0%,#6c1012 60%,#5a0c0e 100%)}
.panel-icon{position:absolute;left:50%;top:59px;width:76px;height:76px;margin-left:-38px;border-radius:50%;background:var(--white);display:flex;align-items:center;justify-content:center}
.panel h2{position:absolute;left:0;right:0;top:148px;font-size:22px;font-weight:600;line-height:25px;letter-spacing:.5px}
.panel p{position:absolute;left:50%;top:208px;transform:translateX(-50%);width:420px;font-size:13.2px;line-height:19.3px}
.panel .btn{position:absolute;left:50%;top:337px;transform:translateX(-50%);width:240px;height:52px;font-size:14.5px}

/* partners */
.partners-title{position:absolute;left:0;right:0;top:1645px;text-align:center;font-size:26px;font-weight:500;color:#333;letter-spacing:.5px}
.partner{position:absolute;top:1715px;width:163px;height:78px;background:var(--white);box-shadow:0 2px 10px rgba(0,0,0,.12);display:flex;align-items:center;justify-content:center}
.partner-badge{width:110px;height:24px;border-radius:4px;background:#d6d9de}

/* testimonials */
.testimonials{position:absolute;left:3px;top:1876px;width:1197px;height:565px;background:var(--grey-band)}
.testimonials-title{position:absolute;left:0;right:0;top:51px;text-align:center;font-size:32px;font-weight:500;line-height:36px;color:var(--ink)}
.testimonials-title em{font-style:normal;color:var(--red);display:block}
.title-rule{position:absolute;left:50%;width:164px;margin-left:-82px;height:2px;background:#aaa}
.title-rule::after{content:"";position:absolute;left:66px;top:-1px;width:32px;height:4px;background:var(--red)}
.quote-card{position:absolute;left:249px;top:167px;width:690px;height:299px;background:var(--white);border:1px solid #bdbdbd;border-radius:4px}
.quote-photo{position:absolute;left:40px;top:32px;width:192px;height:207px;background:linear-gradient(160deg,#f3e4e4 0%,#e9d3d3 100%)}
.quote-text{position:absolute;left:268px;top:64px;width:400px;font-size:14px;line-height:19.4px;color:var(--text)}
.quote-name{position:absolute;left:268px;top:202px;font-size:19px;letter-spacing:2.5px;color:#d24a3c;font-weight:500}
.quote-mark{position:absolute;left:582px;top:208px;font-size:110px;line-height:1;font-family:Georgia,serif;color:#b07777;font-weight:700}
.slider-arrow{position:absolute;top:288px}

/* blog */
.blog-heading{position:absolute;left:115px;top:2511px;font-size:30px;font-weight:700;color:var(--ink)}
.blog-rule{position:absolute;left:115px;top:2562px;width:168px;height:2px;background:#bdbdbd}
.blog-rule::before{content:"";position:absolute;left:0;top:-1px;width:32px;height:4px;background:var(--red)}
.feature-card{position:absolute;left:115px;top:2600px;width:457px;height:390px;border:1px solid #cfcfcf;background:var(--white)}
.feature-image{position:absolute;left:0;top:0;width:455px;height:266px;background:linear-gradient(90deg,#2a0c0d 0%,#5e0f12 45%,#c9ccd1 60%,#8a8f95 100%)}
.date-tag{display:inline-block;background:var(--red-deep);color:var(--white);font-weight:700;font-size:10.5px;padding:4px 12px}
.feature-card .date-tag{position:absolute;left:0;top:238px;font-size:12px;padding:6px 20px}
.feature-card h3{position:absolute;left:28px;top:292px;width:400px;font-size:17px;line-height:23px;font-weight:700;color:var(--ink)}
.learn-more{font-size:10.5px;font-weight:700;color:var(--red);text-decoration:underline;letter-spacing:.3px}
.feature-card .learn-more{position:absolute;left:28px;top:348px}
.post-thumb{position:absolute;left:588px;width:213px;height:189px;border:1px solid #cfcfcf}
.thumb-a{top:2600px;background:linear-gradient(90deg,#3a0d0f 0%,#6a1316 40%,#b9c9d6 60%,#e7ecef 100%)}
.thumb-b{top:2801px;background:linear-gradient(90deg,#5a0d10 0%,#7a1416 55%,#1c1c1c 70%,#3b3f45 100%)}
.post-meta{position:absolute;left:826px;width:300px}
.post-meta h4{font-size:14.5px;line-height:23px;font-weight:700;color:var(--ink);margin-top:10px}
.post-meta p{font-size:11.5px;line-height:17px;color:#4a4a4a;margin-top:4px}
.post-meta .learn-more{display:inline-block;margin-top:6px}

/* contact */
.contact{position:absolute;left:0;top:3061px;width:1200px;height:561px;background:linear-gradient(135deg,#8c181b 0%,#7a1416 50%,#5e0d0f 100%);color:var(--white)}
.contact h2{position:absolute;left:133px;top:110px;font-size:31px;font-weight:600;letter-spacing:1px}
.contact .line{position:absolute;left:133px;top:158px;width:165px;height:2px;background:#d9a9a9}
.field{position:absolute;background:var(--white);color:#444;font-size:12px;padding:14px 18px}
.contact .btn{position:absolute;left:130px;top:387px;width:200px;height:49px;font-size:14.5px}
.contact-halo{position:absolute;left:647px;top:41px;width:470px;height:470px;border-radius:50%;background:rgba(255,255,255,.18)}
.contact-photo{position:absolute;left:660px;top:54px;width:444px;height:444px;border-radius:50%;background:linear-gradient(160deg,#e6e9ee 0%,#c5cdd8 50%,#8ea0bd 100%)}

/* footer */
.footer-top{position:absolute;left:0;top:3622px;width:1200px;height:98px;border-bottom:1px solid #cfcfcf}
.footer-top .btn{position:absolute;top:29px;height:49px;font-size:13px}
.btn-grey{background:#a4a4a4;color:var(--white)}
.footer-col{position:absolute;top:3760px}
.footer-col h5{font-size:15px;font-weight:700;color:var(--ink);letter-spacing:.3px;padding-left:12px;border-left:2px solid var(--red);line-height:18px}
.footer-col ul{list-style:none;margin-top:12px;padding-left:14px}
.footer-col li{font-size:12.2px;line-height:23.2px;color:#4d4d4d}
.footer-bottom{position:absolute;left:0;top:4122px;width:1200px;border-top:1px solid #d5d5d5;text-align:center;padding-top:22px;font-size:11.5px;color:#555}
</style>
</head>
<body>
<div class="page">

  <header class="site-header">
    <a class="brand" href="#" style="left:97px;top:8px"><span class="brand-mark"></span><span class="brand-name">TALL PINE</span></a>
    <nav class="main-nav" style="left:0">
      <a href="#" style="left:382px">ABOUT</a>
      <a href="#" style="left:476px">INDUSTRIES</a>
      <a href="#" class="active" style="left:606px">SERVICES</a>
      <a href="#" style="left:721px">BLOG</a>
      <a href="#" style="left:804px">CONTACT US</a>
    </nav>
    <a class="header-cta" href="#"><strong>GET A FREE CONSULTATION</strong><span>OR CALL US (555) 014-2290</span></a>
  </header>

  <section class="hero" role="img" aria-label="Dark banner with a glowing network mesh background">
    <div class="hero-eyebrow">OUR SERVICES</div>
    <h1 class="hero-title">OUT OF HOME ADVERTISING</h1>
    <a class="btn btn-red" href="#">Grow Your Revenue</a>
  </section>

  <section class="intro">
    <div class="intro-photo-ring"></div>
    <svg class="intro-arc" width="460" height="460" viewBox="0 0 460 460" aria-hidden="true">
      <path d="M 340 40 A 222 222 0 0 1 70 385" fill="none" stroke="var(--red)" stroke-width="12"/>
    </svg>
    <div class="intro-photo" role="img" aria-label="Photo of three smiling colleagues looking at a tablet and phones"></div>
    <div class="intro-copy">
      <h2 class="section-title">OUT OF HOME<em>ADVERTISING</em></h2>
      <div class="rule"></div>
      <p>Out of home advertising is powerful and can reach massive amounts of people multiple times which reinforces your brand and message. Think of some of the billboards you see when you commute around town. Out of home advertisers come top of mind to consumers when they are in need of their services. If you have an event, a new product, a service or cause, out of home advertising can drive website clicks, phone calls and foot traffic can give you an incredible reach among your local demographics.</p>
      <p>What is the right OOH mix from?&nbsp; After a comprehensive client needs analysis we will create a OOH media strategy that could contain some or all of the following; bus stop ads, billboards, Vehicle wraps, mobile billboards and even Arial advertising. Our rates are competitive and our creative is innovative, effective and designed to invoke emotion from your target audience.</p>
    </div>
  </section>

  <section class="panel panel-dark" aria-label="What is OOH">
    <div class="panel-icon">
      <svg width="40" height="40" viewBox="0 0 40 40" fill="none" stroke="#333" stroke-width="2"><rect x="4" y="6" width="28" height="22" rx="2"/><line x1="4" y1="11" x2="32" y2="11"/><rect x="10" y="15" width="14" height="8"/><path d="M26 22 l10 6 -4 1 3 5 -2 1 -3 -5 -3 3 z" fill="#fff"/></svg>
    </div>
    <h2>WHAT IS OUT OF HOME (OOH)<br>ADVERTISING?</h2>
    <p>OOH or Out-Of-Home Advertising consists of all advertising you may see outside of your home. For example, billboards, bus stop, arial ads, street teams and mobile billboards are all great examples of OOH Advertising. Out of home advertising is great for mass exposure and drives tons of awareness for your product, promotion, event, sale or cause.</p>
    <a class="btn btn-outline" href="#">Contact Us Today</a>
  </section>

  <section class="panel panel-red" aria-label="How OOH helps">
    <div class="panel-icon">
      <svg width="40" height="40" viewBox="0 0 40 40" fill="none" stroke="var(--red)" stroke-width="2"><line x1="4" y1="35" x2="36" y2="35"/><rect x="8" y="24" width="5" height="11"/><rect x="16" y="19" width="5" height="16"/><rect x="24" y="14" width="5" height="21"/><polyline points="6,18 14,12 21,14 33,5"/><polyline points="27,5 33,5 33,11"/></svg>
    </div>
    <h2>HOW CAN OUT OF HOME<br>ADVERTISING HELP MY BUSINESS?</h2>
    <p>When you are looking to reach a broad audience then OOH advertising is a solid and highly sought after tactic. When OOH is combined with a digital marketing campaign we can track the effectiveness of an out of home campaign which brings your business better results.</p>
    <a class="btn btn-outline" href="#">Grow Your Revenue</a>
  </section>

  <section class="partners" aria-label="Strategic partners">
    <h2 class="partners-title">STRATEGIC PARTNERS</h2>
    <div class="partner" style="left:117px"><span class="partner-badge"></span></div>
    <div class="partner" style="left:312px"><span class="partner-badge"></span></div>
    <div class="partner" style="left:503px"><span class="partner-badge"></span></div>
    <div class="partner" style="left:698px"><span class="partner-badge"></span></div>
    <div class="partner" style="left:893px"><span class="partner-badge"></span></div>
  </section>

  <section class="testimonials">
    <h2 class="testimonials-title">WHAT ARE INDUSTRY LEADERS<em>SAYING ABOUT TALL PINE</em></h2>
    <div class="title-rule" style="top:133px"></div>
    <svg class="slider-arrow" style="left:150px" width="18" height="26" viewBox="0 0 18 26" fill="none" stroke="#111" stroke-width="3"><polyline points="14,2 4,13 14,24"/></svg>
    <svg class="slider-arrow" style="left:1024px" width="18" height="26" viewBox="0 0 18 26" fill="none" stroke="#111" stroke-width="3"><polyline points="4,2 14,13 4,24"/></svg>
    <article class="quote-card">
      <div class="quote-photo" role="img" aria-label="Portrait photo of the reviewer"></div>
      <p class="quote-text">“Lorem ipsum dolor sit amet, consectetur adipiscing elit, sed do eiusmod tempor incididunt ut labore et dolore magna aliqua. Quis ipsum suspendisse ultrices gravida. Risus commodo viverra maecenas accumsan lacus vel facilisisdisse ultrices gravida. Risus commodo viverra maecenas accumsan lacus vel facilisis”</p>
      <div class="quote-name">DEVMARLOW</div>
      <div class="quote-mark">”</div>
    </article>
  </section>

  <section class="blog" aria-label="Latest blog posts">
    <h2 class="blog-heading">LATEST BLOG POSTS</h2>
    <div class="blog-rule"></div>
    <article class="feature-card">
      <div class="feature-image" role="img" aria-label="Blog cover: content marketing strategy graphic with a laptop and charts"></div>
      <span class="date-tag">20 JAN 2024</span>
      <h3>Rankwell Recognizes Tall Pine as One of the Best PPC Companies in Arizona</h3>
      <a class="learn-more" href="#">LEARN MORE</a>
    </article>
    <div class="post-thumb thumb-a" role="img" aria-label="Blog cover: digital marketing trends graphic with a person at a whiteboard"></div>
    <div class="post-meta" style="top:2610px">
      <span class="date-tag">20 JAN 2024</span>
      <h4>How to Improve E-Commerce<br>Landing Pages with Paid Ads Data</h4>
      <p>Track Your Keyword Rankings in 2021<br>Optimizing your content with a power-<br>ful strategy for keywords</p>
      <a class="learn-more" href="#">LEARN MORE</a>
    </div>
    <div class="post-thumb thumb-b" role="img" aria-label="Blog cover: e-commerce landing pages graphic with a person using a laptop"></div>
    <div class="post-meta" style="top:2816px">
      <span class="date-tag">18 JAN 2024</span>
      <h4>The Best Way to Track Your<br>Keyword Rankings in 2021</h4>
      <p>Track Your Keyword Rankings in 2021<br>Optimizing your content with a power-<br>ful strategy for keywords</p>
      <a class="learn-more" href="#">LEARN MORE</a>
    </div>
  </section>

  <section class="contact" aria-label="Contact form">
    <h2>ELEVATE YOUR MARKETING</h2>
    <div class="line"></div>
    <div class="field" style="left:130px;top:180px;width:219px;height:41px">Name</div>
    <div class="field" style="left:359px;top:180px;width:221px;height:41px">Email</div>
    <div class="field" style="left:130px;top:231px;width:219px;height:41px">Phone</div>
    <div class="field" style="left:359px;top:231px;width:221px;height:41px">Subject</div>
    <div class="field" style="left:130px;top:281px;width:450px;height:81px">Message</div>
    <a class="btn btn-outline" href="#">Send Message</a>
    <div class="contact-halo"></div>
    <div class="contact-photo" role="img" aria-label="Photo of two women reviewing a tablet together"></div>
  </section>

  <footer>
    <div class="footer-top">
      <a class="brand" href="#" style="left:136px;top:28px"><span class="brand-mark"></span><span class="brand-name">TALL PINE</span></a>
      <a class="btn btn-grey" href="#" style="left:609px;width:214px">Call Us (555) 014-2290</a>
      <a class="btn btn-red" href="#" style="left:840px;width:214px">Grow Your Revenue</a>
    </div>
    <div class="footer-col" style="left:144px">
      <h5>QUICK LINKS</h5>
      <ul><li>About</li><li>Industries</li><li>Training</li><li>Blog</li><li>Services</li><li>Contact</li></ul>
    </div>
    <div class="footer-col" style="left:367px">
      <h5>SERVICES</h5>
      <ul><li>Programmatic Advertising</li><li>Search Engine Marketing (SEM)</li><li>Search Engine Optimization (SEO)</li><li>Content Marketing</li><li>Email Marketing</li><li>Paid Search Advertising</li><li>Paid Social Advertising</li></ul>
    </div>
    <div class="footer-col" style="left:652px">
      <h5>INDUSTRIES</h5>
      <ul><li>Ecommerce</li><li>Electricians</li><li>Financial Services Marketing</li><li>Home Builders</li><li>Home Services</li><li>Hvac Companies</li><li>Cosmetic Surgery Centers</li><li>Dental Marketing</li><li>Education</li><li>Healthcare Medical Marketing</li><li>Plumbing Companies</li><li>Podiatrist Marketing</li><li>Landscapers</li></ul>
    </div>
    <div class="footer-col" style="left:906px">
      <h5>LINKS</h5>
      <ul><li>Training</li><li>Resources</li><li>Privacy Policy</li><li>Sitemap</li><li>Terms Of Use</li><li>Press &amp; Media</li><li>Cookie Policy</li></ul>
    </div>
    <div class="footer-bottom">© 2024 Company Name | All Rights Reserved</div>
  </footer>

</div>
</body>
</html>
```